Harbour Lensman's Atlas for iOS

I am a keen travel and lifestyle photographer whose photographic studio is Velmora Imaging, based in Sydney, Australia. You can see my photographic portfolio at velmoraimaging.com.

Overview
-
I want to create an iOS app that will allow Sydney-bound photographers to develop an understanding of some the popular and lesser known sights of this beautiful city and its surrounds. I’d like to achieve this by making available to serious photographers information that will allow them plan their photographic expeditions and explore their own creative interpretations of some classic Sydney photographs. Aiding more serious photographers, the Harbour Lensman’s Atlas will include photographic metadata that most other photo sites exclude, allowing photographers to explore their own settings and creative options with guidance from scene-specific shooting data (Exposure and ISO settings, natural lighting and time of day, focal length etc).

The functionality of the iOS app I’d like to develop are:

1) Ability to review a thumbnail list of Sydney-based photographic galleries (Presented in a “Scenes” tab which the user starts with on launching the app).

a. A section at the bottom will include a “Sydney’s Surrounds” section which will be separated from the other Scenes by some kind of delimiter ( “………..” etc or something more stylish). Under this delimeter will be scenes from surround areas – including “The Hunter Valley”, “The Central Coast”, “The Blue Mountains”, “Woollongong”.

b. At the very bottom of app will be a “Link to Velmora Imaging by Tovin Marsell” which will link to the URL for my site.

2) Ability to select each ‘scene’ and be presented with a gallery of photograph thumbnails from this scene (Presented in a “Gallery” tab which is opened once a Scene is selected from within the “Scenes” tab by touching on that scene’s thumbnail or its associated brief). Note: You can use the “Gallery” drop down menu from my web site for a sense of how I’d like this to look.

3) Having selected a photograph’s thumbnail from the Gallery tab, a user is then taken to an “Image” screen that presents the photograph itself.

a. Within the Image screen, there will be an option to touch an “Info” button, selection of which will trigger the appearance of a semi-opaque overlay tile will appear with the following information:

i. Focal length:
ii. ISO:
iii. F-stop:
iv. Time:
v. Post-production:
vi. A general description field where information is provided around how the photograph was conceived and composed.

b. Within the Image screen, there also be a “Location” button”. On selecting “Location” the user will be taken to a “Map” screen that will present an iOS Maps screen with a pin showing the location the photograph was taken.

c. Finally, within the Image screen, there also be a “Favourite” button”. On selecting “Favourite” the user will ‘star’ the photo and it will be added to the Favourites screen accessed through the Favourites tab (see below)

4) Users will be presented with a fourth tab that will present the “Map” screen. It will be accessed by selecting the “Location” button from within the Image screen, or by directly pressing on the Maps tab itself. There will be Icon which if selected will pinpoint the user’s current location in relation to the photograph’s location (if one has been selected).

5) A “Favourites” screen will be accessed from a fifth Tab that will allow users to see a gallery of all their favourite photographs’ thumbnails.

General Navigation and Look and Feel
-
• I would like a clean and uncluttered modern design that takes guidance from the general look and feel of my website (velmoraimaging.com).
• The UI should be iPad and iPhone friendly. Note: The iPad version would be an expanded resolution of the iPhone version (ie. not relying on a 2x expansion but not necessarily requiring a whole new UI).

I'm looking forward to developing this concept further with your design involvement.
Updates

Hello

I have doubled the committed budget on this design.  Looking forward to your entries.  
Tovin

I do like the idea of a black backgrounded app.  This is the style of my site velmoraimaging.com and blends well into the photo styles used.  It is well presented in the initial design submitted.

Target Market(s)

Serious amateur and semi-pro photographers.

Industry/Entity Type

Travel

Requirements
Must have
• - Galleries that are tiled vertically. You can use the gearlodge app and its list of articles for a view of how this can be presented.

Basically, I'd like

Picture - brief description

You can get a sense of these by looking at my Gallery drop down menu from my website.

- The app needs to look like an app for pro users, and serious photographers. It's not intended to be gimicky, but look professional and elegant.
Should not have
• Not use old style fonts. I would like them clean and modern and economical.

```html
<!DOCTYPE html>
<html lang="en">
<head>
<meta charset="utf-8">
<title>Harbour Lensman's Atlas – Tab Bar</title>
<link href="https://fonts.googleapis.com/css2?family=Roboto+Condensed:wght@700&display=swap" rel="stylesheet">
<style>
  :root {
    --page-bg: #ececec;
    --tab-top: #4a4b4c;
    --tab-mid: #303132;
    --tab-bottom: #1f2020;
    --tab-edge: #151616;
    --tab-highlight: rgba(255,255,255,0.18);
    --active-top: #3c3d3e;
    --active-bottom: #1c1d1d;
    --icon-light: #d6d6d6;
    --icon-dark: #8a8a8a;
    --label: #eeeeee;
  }
  html, body {
    margin: 0;
    padding: 0;
    width: 1200px;
    height: 688px;
    overflow: hidden;
    background: var(--page-bg);
  }
  .canvas {
    position: relative;
    width: 1200px;
    height: 688px;
    background: var(--page-bg);
  }
  .tab-bar {
    position: absolute;
    left: 167px;
    top: 343px;
    width: 926px;
    height: 132px;
    display: flex;
    align-items: flex-end;
    margin: 0;
    padding: 0;
    list-style: none;
  }
  .tab {
    position: relative;
    height: 120px;
    box-sizing: border-box;
    border-radius: 16px 16px 4px 4px;
    background: linear-gradient(to bottom, var(--tab-top) 0%, var(--tab-mid) 45%, var(--tab-bottom) 100%);
    box-shadow: inset 0 2px 0 var(--tab-highlight), inset 0 -1px 0 rgba(0,0,0,0.5), 0 0 0 1px var(--tab-edge);
    display: flex;
    flex-direction: column;
    align-items: center;
    justify-content: flex-start;
  }
  .tab-active {
    height: 132px;
    z-index: 2;
    border-radius: 18px 18px 4px 4px;
    background: linear-gradient(to bottom, var(--active-top) 0%, #2a2b2c 40%, var(--active-bottom) 100%);
    box-shadow: inset 0 2px 0 rgba(255,255,255,0.12), 0 0 0 2px var(--tab-edge), 0 0 10px rgba(0,0,0,0.35);
  }
  .tab-scenes { width: 169px; }
  .tab-gallery { width: 205px; }
  .tab-image { width: 172px; }
  .tab-map { width: 188px; }
  .tab-favourites { width: 192px; }
  .tab-icon {
    margin-top: 16px;
    height: 60px;
    display: flex;
    align-items: center;
    justify-content: center;
  }
  .tab-active .tab-icon { margin-top: 14px; height: 74px; }
  .tab-label {
    position: absolute;
    bottom: 20px;
    left: 0;
    right: 0;
    text-align: center;
    font-family: "Roboto Condensed", "Arial Narrow", sans-serif;
    font-weight: 700;
    font-size: 18px;
    letter-spacing: 0.2px;
    color: var(--label);
    text-shadow: 0 -1px 0 rgba(0,0,0,0.6);
  }
  .landmark-placeholder {
    width: 96px;
    height: 46px;
    margin-top: 8px;
    border-radius: 4px 28px 4px 4px;
    background: linear-gradient(to bottom, var(--icon-light), var(--icon-dark));
  }
</style>
</head>
<body>
<main class="canvas">
  <nav aria-label="Main navigation">
    <ul class="tab-bar">
      <li class="tab tab-scenes">
        <div class="tab-icon">
          <div class="landmark-placeholder" role="img" aria-label="Harbour landmark icon with sail-shaped roofs"></div>
        </div>
        <span class="tab-label">SCENES</span>
      </li>
      <li class="tab tab-gallery tab-active">
        <div class="tab-icon">
          <svg width="72" height="72" viewBox="0 0 72 72" aria-hidden="true">
            <defs>
              <linearGradient id="icon-fill" x1="0" y1="0" x2="0" y2="1">
                <stop offset="0" stop-color="#dcdcdc"/>
                <stop offset="1" stop-color="#8c8c8c"/>
              </linearGradient>
            </defs>
            <g fill="url(#icon-fill)">
              <rect x="2" y="2" width="20" height="20" rx="3"/>
              <rect x="26" y="2" width="20" height="20" rx="3"/>
              <rect x="50" y="2" width="20" height="20" rx="3"/>
              <rect x="2" y="26" width="20" height="20" rx="3"/>
              <rect x="26" y="26" width="20" height="20" rx="3"/>
              <rect x="50" y="26" width="20" height="20" rx="3"/>
              <rect x="2" y="50" width="20" height="20" rx="3"/>
              <rect x="26" y="50" width="20" height="20" rx="3"/>
              <rect x="50" y="50" width="20" height="20" rx="3"/>
            </g>
          </svg>
        </div>
        <span class="tab-label">GALLERY</span>
      </li>
      <li class="tab tab-image">
        <div class="tab-icon">
          <svg width="92" height="60" viewBox="0 0 92 60" aria-hidden="true">
            <defs>
              <linearGradient id="frame-fill" x1="0" y1="0" x2="0" y2="1">
                <stop offset="0" stop-color="#e0e0e0"/>
                <stop offset="1" stop-color="#8a8a8a"/>
              </linearGradient>
            </defs>
            <g transform="rotate(-7 46 30)">
              <rect x="6" y="10" width="80" height="44" fill="url(#frame-fill)"/>
              <rect x="11" y="15" width="70" height="34" fill="#8f8f8f"/>
            </g>
          </svg>
        </div>
        <span class="tab-label">IMAGE</span>
      </li>
      <li class="tab tab-map">
        <div class="tab-icon">
          <svg width="64" height="64" viewBox="0 0 64 64" aria-hidden="true" fill="none" stroke="#cfcfcf" stroke-width="3">
            <circle cx="32" cy="32" r="28"/>
            <ellipse cx="32" cy="32" rx="12" ry="28"/>
            <line x1="32" y1="4" x2="32" y2="60"/>
            <line x1="4" y1="32" x2="60" y2="32"/>
            <path d="M9 18 H55 M9 46 H55"/>
          </svg>
        </div>
        <span class="tab-label">MAP</span>
      </li>
      <li class="tab tab-favourites">
        <div class="tab-icon">
          <svg width="66" height="64" viewBox="0 0 66 64" aria-hidden="true">
            <defs>
              <linearGradient id="star-fill" x1="0" y1="0" x2="0" y2="1">
                <stop offset="0" stop-color="#dddddd"/>
                <stop offset="1" stop-color="#8a8a8a"/>
              </linearGradient>
            </defs>
            <path d="M33 2 L41 23 L64 24 L46 38 L52 61 L33 48 L14 61 L20 38 L2 24 L25 23 Z" fill="url(#star-fill)" stroke-linejoin="round"/>
          </svg>
        </div>
        <span class="tab-label">FAVOURITES</span>
      </li>
    </ul>
  </nav>
</main>
</body>
</html>
```